Print materials for 3-star hotel

We are changing up our print materials (notepads, letterheads, key card jackets, small flyer for the room rates) We are a 3 star business hotel in the Philippines and have mainly used grey tones and clean, simple lines. See attached photos for logo and hotel interior photos.

Target Market(s)

Business

Contact Information for Business Card

Corvale Terrace Hotel
Lindwell Banca Avenue corner Tolenta St Cebu City 6000 Philippines
Tel: +63 32 481 7302
Mobile: +63 917 648 2095
www.corvaleterracehotel.example

Font styles to use
Serif
Sans Serif

Requirements
Must have
• Simple
• Readable font and font size
Nice to have
• Neutral colors, grey and taupes
Should not have
• No purples and bright blues

```html
<!DOCTYPE html>
<html lang="en">
<head>
<meta charset="utf-8">
<title>Corvale Terrace Hotel – Business Card</title>
<link rel="stylesheet" href="https://fonts.googleapis.com/css2?family=Cinzel:wght@400;500&family=Roboto:wght@400;500&display=swap">
<style>
  :root {
    --backdrop: #2b2b2d;
    --taupe: #bfae93;
    --charcoal: #232324;
    --ink-light: #ffffff;
    --ink-soft: #f2f0ec;
  }
  * { margin: 0; padding: 0; box-sizing: border-box; }
  html, body {
    width: 1200px;
    height: 900px;
    overflow: hidden;
    background: var(--backdrop);
  }
  .canvas {
    position: relative;
    width: 1200px;
    height: 900px;
    display: flex;
    flex-direction: column;
    align-items: center;
    justify-content: center;
    gap: 48px;
  }
  .card {
    width: 640px;
    height: 366px;
    position: relative;
  }
  .card--front {
    background: var(--taupe);
    display: flex;
    flex-direction: column;
    align-items: center;
    justify-content: center;
  }
  .brand-mark {
    width: 46px;
    height: 46px;
    background: var(--ink-light);
    margin-bottom: 18px;
  }
  .brand-name {
    font-family: "Cinzel", serif;
    font-weight: 400;
    color: var(--ink-light);
    text-align: center;
    text-transform: uppercase;
    line-height: 1.05;
  }
  .brand-name__main {
    display: block;
    font-size: 25px;
    letter-spacing: 5px;
  }
  .brand-name__sub {
    display: block;
    font-size: 15px;
    letter-spacing: 6px;
  }
  .card--back {
    background: var(--charcoal);
    display: flex;
    flex-direction: column;
    align-items: center;
    justify-content: center;
    text-align: center;
    color: var(--ink-soft);
    padding-top: 40px;
  }
  .person-name {
    font-family: "Cinzel", serif;
    font-weight: 400;
    font-size: 24px;
    letter-spacing: 1.5px;
    color: var(--ink-light);
    line-height: 1.1;
  }
  .person-title {
    font-family: "Roboto", sans-serif;
    font-weight: 500;
    font-size: 14px;
    margin-bottom: 14px;
  }
  .contact-line {
    font-family: "Roboto", sans-serif;
    font-weight: 400;
    font-size: 13.5px;
    line-height: 1.5;
  }
  .contact-line span + span { margin-left: 12px; }
</style>
</head>
<body>
<main class="canvas">
  <section class="card card--front" aria-label="Business card front">
    <div class="brand-mark" aria-hidden="true"></div>
    <h1 class="brand-name">
      <span class="brand-name__main">Corvale Terrace</span>
      <span class="brand-name__sub">Hotel</span>
    </h1>
  </section>

  <section class="card card--back" aria-label="Business card back">
    <h2 class="person-name">ADRIAN VELASCO</h2>
    <p class="person-title">CEO/Founder</p>
    <p class="contact-line">Lindwell Banca Avenue corner Tolenta St, Cebu City 6000</p>
    <p class="contact-line"><span>P: +63 32 481 7302</span><span>M: +63 917 648 2095</span></p>
    <p class="contact-line">E: stay@corvaleterracehotel.example</p>
    <p class="contact-line">www.corvaleterracehotel.example</p>
  </section>
</main>
</body>
</html>
```